Classic and neutral book cover design

We are looking for a classic and neutral book cover design to be used as the template for a series of books to be published. We are hence looking for a template that will allow us to easily change the title name for all books in this series.
The use of very few colours (black and white is welcome) and few design elements is a big bonus. As a source of inspiration we would like to ask you to view the very simple and
If you think you have a cool idea that can add a twist to the formal classic look don't hesitate. Go for it !
Work will be done for a 30 year old Sweden based cultural non-profit called VĂ©ru (www.verufoundation.example). We work with the publishing and supporting of post-modern art and literature addressing contemporary topics but are also involved in assisting projects of cultural preservation.
Target Market(s)
The audience is expected to have some form of interest in culture but could range from hobbyist readers to tenure track scholars
Industry/Entity Type
Non-Profit
Requirements
Must have
- General:
- Classic and neutral feel
- Preferably very simple and few shapes
- usage of few colours (black and white is welcome)
Information to be displayed on the cover is:
- Author
- Title
- type of work e.g. play/novel (optional)
- publishing house (in this case "Veru Publishing")
Nice to have
- ideas to prevent it from become boring are of course welcome
Should not have
- - too many colours

```html
<!DOCTYPE html>
<html lang="en">
<head>
<meta charset="utf-8">
<title>Nice Title — Veru Publishing</title>
<link rel="stylesheet" href="https://fonts.googleapis.com/css2?family=EB+Garamond:ital,wght@0,400;1,400&display=swap">
<style>
  :root {
    --paper: #ffffff;
    --ink: #000000;
    --frame: #000000;
  }
  html, body {
    margin: 0;
    padding: 0;
    width: 952px;
    height: 1200px;
    overflow: hidden;
    background: var(--paper);
  }
  .cover {
    position: relative;
    width: 952px;
    height: 1200px;
    background: var(--paper);
    font-family: "EB Garamond", "Garamond", serif;
    color: var(--ink);
  }
  .cover__frame {
    position: absolute;
    left: 50px;
    top: 50px;
    width: 856px;
    height: 1111px;
    box-sizing: border-box;
    border: 57px solid var(--frame);
    background: var(--paper);
  }
  .cover__line {
    position: absolute;
    left: 0;
    width: 952px;
    margin: 0;
    text-align: center;
    line-height: 1;
    white-space: nowrap;
  }
  .publisher {
    top: 181px;
    font-size: 17px;
    font-style: italic;
    letter-spacing: 3.2px;
    text-transform: uppercase;
  }
  .title {
    font-size: 140px;
    font-weight: 400;
    letter-spacing: 42px;
    text-indent: 42px;
  }
  .title--first { top: 365px; }
  .title--second { top: 547px; }
  .work-type {
    top: 876px;
    font-size: 29px;
    font-style: italic;
  }
  .byline {
    top: 933px;
    font-size: 16px;
    font-style: italic;
  }
  .author {
    top: 968px;
    font-size: 29px;
    letter-spacing: 3.4px;
  }
</style>
</head>
<body>
  <main class="cover">
    <div class="cover__frame" aria-hidden="true"></div>
    <p class="cover__line publisher">Veru Publishing</p>
    <h1 class="cover__line title title--first">NICE</h1>
    <p class="cover__line title title--second" aria-hidden="true">TITLE</p>
    <p class="cover__line work-type">Novel</p>
    <p class="cover__line byline">by</p>
    <p class="cover__line author">Author Authorson</p>
  </main>
</body>
</html>
```